Tarn Workforce Tri Fold Brochure

My company is a recruiting/staffing firm. I need a design that is going to be professional, bright, young, hip and fun. Pictures are key! We want people working in an office, packaging, food production and/or light industrial environment. Must embrace DIVERSITY. Please use the 4 primary colors from the Tarn Logo to accent the piece, but not too busy. I am including the content that I would like to be included in the trifold as well as a sample of a trifold I have used in the past in addition to a couple of logos. My website is www.TarnWorkforce-example.com for look and feel.

Target Market(s)

Logistics, Distribution and Manufacturing companies

Industry/Entity Type

Staffing

Requirements
Must have
• Clean, colorful, eye catching, great pictures and graphics. Photo's of diverse people working, in a office, or production setting.
Nice to have
• Must be professional
Should not have
• Not too busy.

```html
<!DOCTYPE html>
<html lang="en">
<head>
<meta charset="utf-8">
<title>Tarn Workforce Tri-Fold Brochure</title>
<link rel="stylesheet" href="https://fonts.googleapis.com/css2?family=Montserrat:wght@300;400;500;600;700;800&display=swap">
<style>
:root{
  --green:#0d7d5b;
  --green-dark:#08513f;
  --green-light:#13966c;
  --yellow:#f3c414;
  --red:#e2262b;
  --navy:#2b2a73;
  --ink:#333;
  --paper:#fff;
  --backdrop:#ececec;
}
*{margin:0;padding:0;box-sizing:border-box}
html,body{width:1200px;height:2410px;overflow:hidden}
body{background:var(--backdrop);font-family:"Montserrat",sans-serif;color:var(--ink);position:relative}
.spread{position:absolute;left:40px;width:1120px;height:791px;background:var(--paper);box-shadow:0 10px 30px rgba(0,0,0,.18);overflow:hidden}
.spread--outside{top:374px}
.spread--inside{top:1245px}
.panel{position:absolute;top:0;height:791px}
.panel--left{left:0;width:375px}
.panel--middle{left:375px;width:370px}
.panel--right{left:745px;width:375px}
.panel-art{position:absolute;inset:0}
.panel-art svg{display:block}

/* outside: quote panel */
.quote{position:absolute;top:42px;left:42px;right:42px;color:#fff;font-weight:700;font-size:24px;line-height:1.3;text-align:center}
.quote .mark{font-size:34px;line-height:0;vertical-align:-4px}

/* outside: contact panel */
.locations{position:absolute;top:42px;left:0;right:0;text-align:center}
.state{color:var(--green);font-weight:700;font-size:25px;margin-bottom:4px}
.branch{font-size:13px;line-height:1.25;color:#333}
.location{margin-bottom:30px}
.brand{font-weight:700;color:var(--navy);letter-spacing:.5px;white-space:nowrap}
.brand--contact{position:absolute;top:430px;left:0;right:0;text-align:center;font-size:36px}
.contact{position:absolute;top:565px;left:0;right:0;text-align:center}
.icon-dot{display:block;margin:0 auto 8px}
.phone{font-weight:600;font-size:20px;letter-spacing:3px;margin-bottom:22px}
.address{font-size:13px;letter-spacing:1.5px;line-height:1.3;margin-bottom:26px}
.web{font-weight:600;font-size:15px;letter-spacing:1.4px;white-space:nowrap}

/* outside: cover */
.brand--cover{position:absolute;top:48px;left:30px;font-size:32px}
.cover-title{position:absolute;top:570px;left:0;right:0;text-align:center;color:#fff}
.cover-title .light{display:block;font-weight:300;font-size:42px;letter-spacing:1px;line-height:1.05}
.cover-title .bold{display:block;font-weight:800;font-size:60px;color:var(--yellow);line-height:1.02}
.pill-url{display:inline-block;margin-top:14px;background:var(--yellow);color:var(--green-dark);font-weight:700;font-size:12px;letter-spacing:1.2px;padding:6px 16px;border-radius:16px;white-space:nowrap}

/* inside */
.copy{position:absolute;left:24px;right:24px;font-size:10px;line-height:1.32}
.tag{display:inline-block;background:var(--yellow);color:var(--red);font-weight:600;font-size:15px;padding:3px 16px;border-radius:12px;margin:0 0 7px;min-width:150px}
.copy p{margin-bottom:10px}
.copy--light{color:#fff}
.sub{font-weight:600;font-size:14px;color:#333;margin:6px 0 10px}
.sub--white{color:#fff;font-size:15px;margin:0 0 16px}
.list{display:grid;grid-template-columns:repeat(3,1fr);gap:3px 8px;list-style:none;margin:2px 0 14px;font-size:10px}
.list li{position:relative;padding-left:13px;line-height:1.2}
.list li::before{content:"";position:absolute;left:0;top:2px;width:5px;height:5px;border:2px solid var(--red);border-radius:50%}
.footer{position:absolute;left:24px;right:24px;bottom:18px;display:flex;align-items:flex-end;gap:8px}
.footer .brand{font-size:15px}
.footer .rule{flex:1;border-bottom:1px solid #666;margin-bottom:4px}
.footer .web{font-size:10px;letter-spacing:1px}
</style>
</head>
<body>

<section class="spread spread--outside" aria-label="Brochure outside">
  <div class="panel panel--left">
    <div class="panel-art">
      <svg width="375" height="791" viewBox="0 0 375 791">
        <defs>
          <linearGradient id="greenFacet" x1="0" y1="0" x2="1" y2="1">
            <stop offset="0" stop-color="#13966c"/><stop offset=".5" stop-color="#0d7d5b"/><stop offset="1" stop-color="#08513f"/>
          </linearGradient>
        </defs>
        <g role="img" aria-label="Photo: young technician in a yellow hard hat and gloves testing equipment with a meter">
          <rect width="375" height="791" fill="#f1f1f0"/>
          <rect x="60" y="430" width="240" height="361" fill="#dcd6cf"/>
        </g>
        <polygon points="0,0 375,0 375,200 0,480" fill="url(#greenFacet)"/>
        <polygon points="0,480 375,200 375,216 0,502" fill="var(--red)"/>
        <polygon points="0,502 375,216 375,226 0,515" fill="var(--yellow)"/>
      </svg>
    </div>
    <p class="quote"><span class="mark">&ldquo;</span> YES the CANDIDATE meets the requirements, YEAH they HAVE the skills, but do they TARN? <span class="mark">&rdquo;</span></p>
  </div>

  <div class="panel panel--middle">
    <div class="locations">
      <div class="location"><h2 class="state">Georgia</h2><p class="branch">Harlow Springs – 555-014-2201<br>Quillan – 555-014-2202<br>Brennick Bay – 555-014-2203<br>Orrin Falls – 555-014-2204</p></div>
      <div class="location"><h2 class="state">Indiana</h2><p class="branch">Velmont – 555-014-2205</p></div>
      <div class="location"><h2 class="state">Pennsylvania</h2><p class="branch">Cadwell – 555-014-2206<br>Ashcombe – 555-014-2207</p></div>
      <div class="location"><h2 class="state">Texas</h2><p class="branch">Dunmore Ridge – 555-014-2208</p></div>
    </div>
    <p class="brand brand--contact">Tarn Workforce</p>
    <div class="contact">
      <svg class="icon-dot" width="18" height="18" viewBox="0 0 18 18" aria-hidden="true"><circle cx="9" cy="9" r="9" fill="var(--green)"/><path d="M6 5l2 0 1 2.5-1.2 1a6 6 0 0 0 2.7 2.7l1-1.2 2.5 1v2c0 .6-.5 1-1 1A8 8 0 0 1 5 6c0-.6.4-1 1-1z" fill="#fff"/></svg>
      <p class="phone">555-014-2201</p>
      <svg class="icon-dot" width="18" height="18" viewBox="0 0 18 18" aria-hidden="true"><circle cx="9" cy="9" r="9" fill="var(--green)"/><path d="M9 4a3.5 3.5 0 0 1 3.5 3.5C12.5 10 9 14 9 14S5.5 10 5.5 7.5A3.5 3.5 0 0 1 9 4z" fill="#fff"/><circle cx="9" cy="7.5" r="1.3" fill="var(--green)"/></svg>
      <p class="address">480 Alder Row, Suite 12,<br>Harlow Springs, GA 00000</p>
      <p class="web">www.TarnWorkforce-example.com</p>
    </div>
  </div>

  <div class="panel panel--right">
    <div class="panel-art">
      <svg width="375" height="791" viewBox="0 0 375 791">
        <polygon points="0,262 375,60 375,791 0,791" fill="url(#greenFacet)"/>
        <g role="img" aria-label="Photo: diverse team meeting around an office table with laptops">
          <polygon points="0,278 375,76 375,412 0,565" fill="#8b8a84"/>
        </g>
        <polygon points="0,565 375,412 375,428 0,585" fill="var(--red)"/>
        <polygon points="0,585 375,428 375,437 0,597" fill="var(--yellow)"/>
      </svg>
    </div>
    <p class="brand brand--cover">Tarn Workforce</p>
    <h1 class="cover-title">
      <span class="light">ATTAINING</span>
      <span class="bold">CLIENT</span>
      <span class="light">OBJECTIVES</span>
      <span class="pill-url">www.TarnWorkforce-example.com</span>
    </h1>
  </div>
</section>

<section class="spread spread--inside" aria-label="Brochure inside">
  <div class="panel panel--left">
    <div class="panel-art">
      <svg width="375" height="791" viewBox="0 0 375 791">
        <polygon points="0,370 375,420 375,791 0,791" fill="url(#greenFacet)"/>
        <polygon points="0,354 375,404 375,414 0,364" fill="var(--red)"/>
        <polygon points="0,364 375,414 375,420 0,370" fill="var(--yellow)"/>
      </svg>
    </div>
    <div class="copy" style="top:16px">
      <h3 class="tag">Definition of TARN – verb</h3>
      <p>To be in harmony or accord; To Fit; Agree “Yes the candidate meets the requirements, yeah they have the skills, but do they Tarn?”</p>
      <h3 class="tag">Mission</h3>
      <p>At Tarn Workforce, we are passionate in our pursuit to change lives by connecting great people with great organizations.</p>
      <h3 class="tag">Who We Are</h3>
      <p>At Tarn Workforce, we are interested in helping people and improving lives. We partner with great organizations who are looking to make themselves even better by placing driven and passionate individuals interested in improving their lives and careers. Tarn Workforce is a values-based organization that approaches every interaction with integrity and strives to ensure that every placement makes a positive impact.</p>
    </div>
    <div class="copy copy--light" style="top:440px">
      <h3 class="tag">What We Do</h3>
      <p>At Tarn Workforce we do things a little differently. We don’t just act as a pipeline, blindly pumping workers into your organization who exit almost as quickly as they appear. We provide a system of professional development and training that prepares our talent to enter each placement with the skills and the attitude they need to succeed. In addition to our years of light industrial and professional staffing experience, Tarn Workforce is also a leader in creating client specific onsite programs and high-volume recruitment programs that are designed to meet the specific needs of our individual clients.</p>
      <p>We believe in providing our partners with not only the most prepared talent, but also the most secure. At Tarn Workforce, we do more than simply satisfy the minimum legal requirements for screening. We incorporate an extensive battery of tests and checks, including background and drug, as well as ensuring that every individual we recommend and place is E-Verified.</p>
    </div>
  </div>

  <div class="panel panel--middle">
    <div class="copy" style="top:26px">
      <p>Tarn Workforce is powered by a recruiting engine that never stops. With the right combination of passion and process, we not only have the motivation to meet the Temporary Staffing, Temp-to-Hire and Direct Hire needs of great companies, but we also have the resources and experience to deliver on the promise of a better experience. We provide a higher level of service through our on-boarding and pre-training programs, which are designed to maximize the value of our placements.</p>
      <p>At Tarn Workforce, we have a golden opportunity to positively impact the lives of employers and job seekers. This opportunity is a privilege and an honor and is why we love what we do.</p>
      <p>We look forward to learning about your specific needs and exploring how Tarn Workforce can bring immediate and lasting value.</p>
      <h3 class="tag">Staffing Options</h3>
      <h4 class="sub">Temporary</h4>
      <p>This is an ideal solution that provides flexibility for companies that may have projects, seasonal spikes or a need to fill in the gaps when job vacancies occur. It is a great way for companies to ramp up without adding new associates to the payroll. It also saves on associate costs and provides an opportunity to evaluate talent.</p>
      <h4 class="sub">Temp to Hire</h4>
      <p>Is a way for clients to test the waters and see if the candidate will prove themselves and be a good long-term fit with the company. This program enables the client to examine the performance and attitude of the candidate for a predetermined period of time while on Tarn’s payroll prior to being offered a full-time position with the client.</p>
    </div>
    <div class="panel-art" style="top:595px;height:196px" role="img" aria-label="Photo: three warehouse workers in hard hats reviewing a tablet">
      <svg width="370" height="196" viewBox="0 0 370 196"><rect width="370" height="196" fill="#b9aa98"/><rect x="0" y="120" width="370" height="76" fill="#4d5a6e"/></svg>
    </div>
  </div>

  <div class="panel panel--right">
    <div class="panel-art">
      <svg width="375" height="791" viewBox="0 0 375 791">
        <polygon points="0,0 375,0 375,250 0,205" fill="url(#greenFacet)"/>
        <polygon points="0,205 375,250 375,262 0,216" fill="var(--red)"/>
        <polygon points="0,216 375,262 375,270 0,223" fill="var(--yellow)"/>
      </svg>
    </div>
    <div class="copy copy--light" style="top:28px">
      <h3 class="sub sub--white">Direct Hire</h3>
      <p>When a client has a long-term or highly skilled need, direct hire is an ideal program. Many top performers will not leave a full-time job for a temp or temp to hire opportunity. This is a great way for companies to attract top talent! Tarn will recruit and screen candidates to be interviewed with the client. When the client chooses to move forward and offer a full-time position, the candidate will go directly on the client’s payroll and become a full-time associate on day 1.</p>
    </div>
    <div class="copy" style="top:282px">
      <h3 class="tag">Onsite Management</h3>
      <p>Tarn Workforce offers Onsite Management for clients that utilize a high volume of Tarn associates. Our Onsite Manager will in essence serve as an extension of our client’s management team. They are on the production floor 75% of the time, not in an office. Tarn Workforce’s Onsite Manager is charged with training Tarn Associate’s, coaching, counseling, driving production as well as quality and overall safety.</p>
      <h3 class="tag">Light Industrial</h3>
      <ul class="list"><li>Manufacturing</li><li>Logistics</li><li>Packaging</li><li>Assembly</li><li>Printing</li><li>Fulfillment</li><li>Hospitality</li></ul>
      <h3 class="tag">Skilled Trades</h3>
      <ul class="list"><li>Electrical</li><li>Maintenance</li><li>Welding</li><li>Painting</li><li>C&amp;C Operators/ Programmers</li><li>Machine Operators</li><li>Plumbing</li></ul>
      <h3 class="tag">Professional</h3>
      <ul class="list"><li>Accounting</li><li>Administrative</li><li>Call Center</li><li>Customer Service</li><li>Data Entry</li><li>Executive Management</li><li>Legal</li><li>Sales</li></ul>
    </div>
    <div class="footer"><span class="brand">Tarn Workforce</span><span class="rule"></span><span class="web">www.TarnWorkforce-example.com</span></div>
  </div>
</section>

</body>
</html>
```